Luxury WordPress Website for CORALBASINS

I need a professional WordPress website for Coral Basins. The site should be modern, visually appealing, and user-friendly, reflecting the brand’s luxury and premium identity. It must include a homepage, product/service pages, contact form, and be responsive on both desktop and mobile devices. The design should allow for easy updates and integration of future content, while maintaining a polished and professional look.

Target Market(s)

swimmingpool & spa

Industry/Entity Type

Swimmingpool

Coding

Coded - Design and coding required

Font styles to use
Other font styles liked:
• HaboroSoft

Requirements
Must have
• Exclusive appearance
Nice to have
• • A logo that subtly incorporates water or pool elements. • A color palette that reflects luxury, elegance, and relaxation. • Clean and modern typography that is easy to read across all media. • Iconography or design elements that convey premium quality. • A versatile design that can be adapted for social media, merchandise, and promotional materials. • Optional: A tagline that emphasizes luxury and high-end pool experiences.

```html
<!DOCTYPE html>
<html lang="en">
<head>
<meta charset="utf-8">
<title>Coral Basins — Where Luxury Meets Water</title>
<link href="https://fonts.googleapis.com/css2?family=Playfair+Display:wght@400;500&family=Poppins:wght@400;500;600&display=swap" rel="stylesheet">
<style>
:root{
  --blue:#2b7aa6;
  --blue-dark:#1d5b85;
  --ink:#1b1f24;
  --text:#4a4f55;
  --muted:#6b7077;
  --band:#eeeff1;
  --footer:#0b1620;
  --line:#c9ccd0;
  --white:#ffffff;
}
*{margin:0;padding:0;box-sizing:border-box}
html,body{width:1200px;height:5305px;overflow:hidden}
body{font-family:'Poppins',sans-serif;color:var(--ink);background:var(--white);position:relative}
.abs{position:absolute}
.serif{font-family:'Playfair Display',serif;font-weight:400}
.btn{position:absolute;height:44px;border-radius:22px;background:linear-gradient(90deg,var(--blue-dark),var(--blue));color:var(--white);font-size:11px;font-weight:600;letter-spacing:.5px;display:flex;align-items:center;justify-content:center;text-transform:uppercase}
.label{position:absolute;left:0;width:1200px;text-align:center;color:var(--blue);font-weight:500;font-size:21px;letter-spacing:.3px;text-transform:uppercase}
.title{position:absolute;left:0;width:1200px;text-align:center;font-family:'Playfair Display',serif;font-size:40px;color:var(--ink)}
.ph{position:absolute}

/* header / hero */
.hero{position:absolute;left:0;top:0;width:1200px;height:686px;background:linear-gradient(180deg,#1c3a57 0%,#3a4a55 40%,#7a5a3e 62%,#2f6f86 80%,#6e7a80 100%)}
.brand{position:absolute;display:flex;align-items:center;gap:14px}
.brand .mark{width:54px;height:54px;border-radius:50%;background:var(--blue)}
.brand .name{font-family:'Playfair Display',serif;font-size:25px;color:var(--white);line-height:1}
.brand .tag{font-size:8.5px;color:var(--white);letter-spacing:.3px;margin-top:8px}
.nav{position:absolute;top:54px;left:467px;display:flex;gap:24px;font-size:14px;font-weight:500;color:var(--white)}
.call{position:absolute;left:882px;top:44px;display:flex;align-items:center;gap:12px;color:var(--white)}
.call .ic{width:44px;height:44px;border-radius:50%;background:var(--blue);display:flex;align-items:center;justify-content:center}
.call small{display:block;font-size:9px;opacity:.85}
.call b{font-size:14px;font-weight:500}
.hero h1{position:absolute;top:318px;left:0;width:1200px;text-align:center;font-family:'Playfair Display',serif;font-weight:400;font-size:56px;color:var(--white)}

/* about */
.about p{position:absolute;left:650px;top:972px;width:450px;font-size:14.5px;line-height:27.5px;color:var(--text)}

/* collections */
.coll-cap{position:absolute;top:1904px;width:239px;text-align:center;font-size:14.5px;font-weight:600;text-transform:uppercase}

/* experience */
.band{position:absolute;left:0;top:2044px;width:1200px;height:580px;background:var(--band)}
.exp-text{position:absolute;left:0;top:2254px;width:1200px;text-align:center;font-size:13.5px;line-height:29px;color:var(--text)}
.step{position:absolute;top:2355px;width:240px;text-align:center}
.step .circ{width:114px;height:114px;border-radius:50%;background:linear-gradient(180deg,var(--blue),var(--blue-dark));margin:0 auto;display:flex;align-items:center;justify-content:center}
.step h4{margin-top:20px;font-size:15px;font-weight:600;text-transform:uppercase}

/* testimonials */
.t-bg{position:absolute;left:0;top:3762px;width:1200px;height:430px;background:linear-gradient(180deg,#2b3338 0%,#4b5457 55%,#37403a 100%)}
.t-card{position:absolute;top:4013px;width:433px;height:247px;background:var(--white);box-shadow:0 14px 30px rgba(0,0,0,.12)}
.t-card .av{position:absolute;left:32px;top:24px;width:68px;height:68px;border-radius:50%;background:linear-gradient(135deg,#c97a52,#7a3a2a)}
.t-card h5{position:absolute;left:113px;top:46px;font-size:16px;font-weight:600}
.t-card p{position:absolute;left:32px;top:110px;width:375px;font-size:12.5px;line-height:24px;color:var(--text)}

/* contact */
.field{position:absolute;border:1px solid var(--line);background:var(--white);font-size:12.5px;color:var(--muted);padding:18px 18px}

/* footer */
.footer{position:absolute;left:0;top:4923px;width:1200px;height:382px;background:var(--footer);color:var(--white)}
.f-nav{position:absolute;left:0;top:170px;width:1200px;display:flex;justify-content:center;gap:25px;font-size:14px;font-weight:500}
.f-line{position:absolute;left:172px;width:886px;height:1px;background:rgba(255,255,255,.18)}
.f-info{position:absolute;top:224px;left:0;width:1200px;display:flex;justify-content:center;gap:70px;font-size:13.5px;align-items:center}
.f-info span{display:flex;align-items:center;gap:8px}
.f-copy{position:absolute;top:295px;left:0;width:1200px;text-align:center;font-size:12px}
.social{position:absolute;top:337px;left:0;width:1200px;display:flex;justify-content:center;gap:14px}
.social i{width:14px;height:14px;border-radius:50%;background:var(--white);display:block}
</style>
</head>
<body>

<header class="hero" role="img" aria-label="Luxury villa at dusk with illuminated infinity pool and spa"></header>
<div class="brand" style="left:130px;top:36px">
  <div class="mark"></div>
  <div><div class="name">Coral Basins</div><div class="tag">ALL YOUR DREAMS COME TRUE</div></div>
</div>
<nav class="nav"><span>Home</span><span>About us</span><span>Services</span><span>Gallery</span><span>Contact</span></nav>
<div class="call">
  <div class="ic"><svg width="18" height="18" viewBox="0 0 24 24"><path fill="#fff" d="M6.6 10.8a15.1 15.1 0 0 0 6.6 6.6l2.2-2.2c.3-.3.7-.4 1-.2 1.1.4 2.3.6 3.6.6.6 0 1 .4 1 1V20c0 .6-.4 1-1 1A17 17 0 0 1 3 4c0-.6.4-1 1-1h3.5c.6 0 1 .4 1 1 0 1.3.2 2.5.6 3.6.1.3 0 .7-.2 1z"/></svg></div>
  <div><small>Call Us Today</small><b>+1 (555) 014 2290</b></div>
</div>
<h1>Where Luxury Meets Water</h1>
<div class="btn" style="left:506px;top:410px;width:190px">Get Your Free Quote</div>

<section class="about">
  <div class="ph" style="left:109px;top:813px;width:218px;height:198px;background:linear-gradient(180deg,#6b5a4a,#3d7ea6)" role="img" aria-label="Mansion with rectangular pool"></div>
  <div class="ph" style="left:109px;top:1033px;width:218px;height:200px;background:linear-gradient(180deg,#b49b86,#3e4c58)" role="img" aria-label="Infinity pool with palms at sunset"></div>
  <div class="ph" style="left:348px;top:813px;width:241px;height:420px;background:linear-gradient(180deg,#8fae6a,#6fae3a 55%,#2d8cc0)" role="img" aria-label="Pool technician in hard hat with tablet"></div>
  <div class="abs" style="left:648px;top:806px;color:var(--blue);font-size:21px;font-weight:500">ABOUT US</div>
  <div class="abs serif" style="left:646px;top:842px;font-size:41px;line-height:53px">Crafted for<br>The Extraordinary</div>
  <p>Lorem ipsum dolor sit amet, consectetur adipiscing elit, sed do eiusmod tempor incididunt ut labore et dolore magna aliqua. Ut enim ad minim veniam, quis nostrud exercitation ullamco laboris nisi ut aliquip ex ea commodo consequat. Duis aute irure dolor in reprehenderit in voluptate velit esse cillum dolore eu fugiat nulla pariatur. Excepteur sint occaecat cupidatat non proident, sunt in culpa qui officia deserunt mollit anim id est laborum.</p>
  <div class="btn" style="left:648px;top:1202px;width:145px">Learn More</div>
</section>

<section class="collections">
  <div class="label" style="top:1396px">Our Collections</div>
  <div class="title" style="top:1432px">Our Signature Pool Designs</div>
  <div class="abs" style="left:0;top:1504px;width:1200px;text-align:center;font-size:13px;color:var(--text)">Bespoke creations tailored to your lifestyle.</div>
  <div class="ph" style="left:105px;top:1558px;width:239px;height:321px;background:linear-gradient(180deg,#3a4f72,#2a6fa6 60%,#1f3f6a)" role="img" aria-label="Infinity edge pool facing city skyline"></div>
  <div class="ph" style="left:358px;top:1558px;width:239px;height:321px;background:linear-gradient(180deg,#5b6870,#1d2a30 50%,#4fa0b8)" role="img" aria-label="Geometric modern pool house"></div>
  <div class="ph" style="left:611px;top:1558px;width:238px;height:321px;background:linear-gradient(180deg,#3d4a2c,#2b6e78 60%,#1e4a4a)" role="img" aria-label="Natural pool among tropical plants"></div>
  <div class="ph" style="left:862px;top:1558px;width:239px;height:321px;background:linear-gradient(180deg,#f0a04a,#c0683a 45%,#3a7e9a)" role="img" aria-label="Resort pool with palms at sunset"></div>
  <div class="coll-cap" style="left:105px">Infinity Edge Pools</div>
  <div class="coll-cap" style="left:358px">Geometric Elegance</div>
  <div class="coll-cap" style="left:611px">Natural Oasis</div>
  <div class="coll-cap" style="left:862px">Resort Retreats</div>
</section>

<section>
  <div class="band"></div>
  <div class="label" style="top:2150px">The Experience</div>
  <div class="title" style="top:2185px">The Coral Experience</div>
  <div class="exp-text">From concept to completion, our process ensures seamless perfection.<br>Every project is managed with meticulous attention, ensuring that every tile, curve, and reflection aligns with your vision.</div>
  <div class="step" style="left:119px"><div class="circ"><svg width="54" height="54" viewBox="0 0 24 24" fill="none" stroke="#fff" stroke-width="1.4"><path d="M4 5h16v10H9l-5 4z"/><path d="M8 9h8M8 12h5"/></svg></div><h4>Consultation</h4></div>
  <div class="step" style="left:360px"><div class="circ"><svg width="54" height="54" viewBox="0 0 24 24" fill="none" stroke="#fff" stroke-width="1.4"><rect x="4" y="4" width="16" height="16"/><path d="M8 16l8-8 1.5 1.5-8 8H8z"/></svg></div><h4>Design</h4></div>
  <div class="step" style="left:600px"><div class="circ"><svg width="54" height="54" viewBox="0 0 24 24" fill="none" stroke="#fff" stroke-width="1.4"><path d="M3 8h18M3 12h18M3 16h18M8 8v4M15 8v4M11 12v4M18 12v4M6 16v4M13 16v4M3 20h18"/></svg></div><h4>Build</h4></div>
  <div class="step" style="left:841px"><div class="circ"><svg width="54" height="54" viewBox="0 0 24 24" fill="none" stroke="#fff" stroke-width="1.4"><circle cx="12" cy="12" r="8"/><path d="M8 12l3 3 5-6"/></svg></div><h4>Perfection</h4></div>
</section>

<section class="projects">
  <div class="label" style="top:2720px">Our Project</div>
  <div class="title" style="top:2755px">Discover Perfection in Every Reflection.</div>
  <div class="ph" style="left:138px;top:2840px;width:529px;height:237px;background:linear-gradient(180deg,#5e7a48,#3a9ac0 50%,#7a6650)" role="img" aria-label="Curved garden pool with wooden deck"></div>
  <div class="ph" style="left:677px;top:2840px;width:385px;height:237px;background:linear-gradient(180deg,#c8c2b6,#4aa0a0 60%,#1f6a70)" role="img" aria-label="Indoor glass pool pavilion"></div>
  <div class="ph" style="left:138px;top:3085px;width:385px;height:237px;background:linear-gradient(180deg,#3a4a58,#8a5a3a 50%,#2f8ab8)" role="img" aria-label="Screened pool enclosure with lounge"></div>
  <div class="ph" style="left:533px;top:3085px;width:529px;height:237px;background:linear-gradient(180deg,#7aa0c0,#4a5a3a 45%,#4a8ea0)" role="img" aria-label="Desert garden pool with umbrella"></div>
  <div class="ph" style="left:138px;top:3330px;width:529px;height:237px;background:linear-gradient(180deg,#3e3428,#8a7a66 45%,#3a96b8)" role="img" aria-label="Poolside lounge with sofas"></div>
  <div class="ph" style="left:677px;top:3330px;width:385px;height:237px;background:linear-gradient(180deg,#3c4a5a,#6a5040 45%,#141e3a)" role="img" aria-label="Modern house with dark pool at night"></div>
  <div class="btn" style="left:529px;top:3614px;width:142px">View More</div>
</section>

<section class="testimonials">
  <div class="t-bg" role="img" aria-label="Modern villa at evening with garden"></div>
  <div class="label" style="top:3873px;color:var(--white)">Our Testimonials</div>
  <div class="title" style="top:3907px;color:var(--white)">What Our Clients Say</div>
  <div class="t-card" style="left:156px"><div class="av" role="img" aria-label="Client portrait"></div><h5>Elena Marsh</h5><p>Lorem ipsum dolor sit amet, consectetur adipiscing elit, sed do eiusmod tempor incididunt ut labore et dolore magna aliqua. Ut enim ad minim veniam, quis nostrud exercitation ullamco laboris nisi ut aliquip</p></div>
  <div class="t-card" style="left:611px"><div class="av" role="img" aria-label="Client portrait"></div><h5>Daniel Reyes</h5><p>Lorem ipsum dolor sit amet, consectetur adipiscing elit, sed do eiusmod tempor incididunt ut labore et dolore magna aliqua. Ut enim ad minim veniam, quis nostrud exercitation ullamco laboris nisi ut aliquip</p></div>
</section>

<section class="contact">
  <div class="label" style="top:4362px">Contact Us</div>
  <div class="title" style="top:4397px">Connect With Us</div>
  <div class="field" style="left:228px;top:4489px;width:367px;height:57px">Name</div>
  <div class="field" style="left:603px;top:4489px;width:367px;height:57px">Email</div>
  <div class="field" style="left:228px;top:4561px;width:367px;height:57px">Phone</div>
  <div class="field" style="left:603px;top:4561px;width:367px;height:57px">Service</div>
  <div class="field" style="left:228px;top:4633px;width:742px;height:107px">Message</div>
  <div class="btn" style="left:529px;top:4765px;width:142px">Submit</div>
</section>

<footer class="footer">
  <div class="brand" style="left:478px;top:86px">
    <div class="mark"></div>
    <div><div class="name">Coral Basins</div><div class="tag">ALL YOUR DREAMS COME TRUE</div></div>
  </div>
  <nav class="f-nav"><span>Home</span><span>About us</span><span>Services</span><span>Gallery</span><span>Contact</span></nav>
  <div class="f-line" style="top:201px"></div>
  <div class="f-info">
    <span><svg width="14" height="12" viewBox="0 0 24 20"><path fill="#fff" d="M2 2h20v16H2z M2 2l10 8 10-8" stroke="#0b1620" stroke-width="1.5"/></svg>contact@coralbasins.com</span>
    <span><svg width="13" height="13" viewBox="0 0 24 24"><path fill="#fff" d="M6.6 10.8a15.1 15.1 0 0 0 6.6 6.6l2.2-2.2c.3-.3.7-.4 1-.2 1.1.4 2.3.6 3.6.6.6 0 1 .4 1 1V20c0 .6-.4 1-1 1A17 17 0 0 1 3 4c0-.6.4-1 1-1h3.5c.6 0 1 .4 1 1 0 1.3.2 2.5.6 3.6.1.3 0 .7-.2 1z"/></svg>+1 (555) 014 2290</span>
    <span><svg width="11" height="14" viewBox="0 0 24 30"><path fill="#fff" d="M12 0a10 10 0 0 0-10 10c0 8 10 20 10 20s10-12 10-20A10 10 0 0 0 12 0zm0 14a4 4 0 1 1 0-8 4 4 0 0 1 0 8z"/></svg>Global Presence: California | Dubai | Sydney</span>
  </div>
  <div class="f-line" style="top:255px"></div>
  <div class="f-copy">Copyright@2025.All Rights Reserved</div>
  <div class="social"><i></i><i></i><i></i></div>
</footer>

</body>
</html>
```